Professional and creative business card design for recruiting service providers

Our company supports German medium-sized companies in filling vacancies promptly. For this we use social media marketing and bring our customers into the visibility.

We want a professional but also creative design for our business cards.

Please look at lindqvar-staff.de to get an impression of our CI.

Target Market(s)

Small and medium-sized companies in Germany from the industry

Industry/Entity Type

Industrie, Handwerk

Contact Information for Business Card

Name, Position, Telefonnummer, Email, Website

Colors
EE7325
F08F49
F5BC92
FAE3D3
FDF4ED

Requirements
Must have
• A picture of the employee and in the style of www.lindqvar-staff.de

```html
<!DOCTYPE html>
<html lang="de">
<head>
<meta charset="utf-8">
<title>Lindqvar &amp; Staff – Visitenkarte</title>
<link rel="stylesheet" href="https://fonts.googleapis.com/css2?family=Poppins:wght@400;600;700&display=swap">
<style>
  :root {
    --orange: #EE7325;
    --orange-light: #F08F49;
    --ink: #0b0b0b;
    --white: #ffffff;
    --paper-grey: #f1f1f1;
    --photo-top: #e4e2e2;
    --photo-bottom: #c9c6c5;
    --stage: #2a2a2a;
    --text-dark: #141414;
  }
  * { box-sizing: border-box; margin: 0; padding: 0; }
  html, body { width: 1200px; height: 866px; overflow: hidden; }
  body {
    background: var(--stage);
    font-family: "Poppins", sans-serif;
    display: flex;
    align-items: center;
    justify-content: center;
    gap: 40px;
  }
  .card {
    position: relative;
    width: 540px;
    height: 318px;
    overflow: hidden;
    box-shadow: 0 14px 30px rgba(0,0,0,.45);
  }

  /* Front side */
  .card-front { background: var(--white); }
  .front-shade {
    position: absolute; left: 150px; top: 0; width: 220px; height: 318px;
    background: linear-gradient(160deg, var(--paper-grey), rgba(241,241,241,0));
  }
  .brand {
    position: absolute; display: flex; align-items: center; gap: 12px;
  }
  .brand-mark { width: 30px; height: 30px; background: var(--orange); flex: none; }
  .brand-name {
    font-weight: 700; text-transform: uppercase; letter-spacing: 2px; line-height: 1.05;
  }
  .card-front .brand { left: 34px; top: 34px; }
  .card-front .brand-name { font-size: 19px; color: var(--text-dark); }

  .person { position: absolute; left: 34px; top: 112px; }
  .person-name {
    font-size: 18px; font-weight: 700; letter-spacing: 1.5px;
    text-transform: uppercase; color: var(--text-dark);
  }
  .person-role { font-size: 12px; color: var(--text-dark); letter-spacing: .5px; }
  .divider {
    position: absolute; left: 34px; top: 168px; width: 230px; height: 1px;
    background: var(--orange);
  }
  .contact { position: absolute; left: 34px; top: 180px; list-style: none; }
  .contact li {
    display: flex; align-items: center; gap: 8px;
    font-size: 12px; color: var(--text-dark); line-height: 20px;
  }
  .contact svg { width: 12px; height: 12px; flex: none; }

  .photo {
    position: absolute; left: 300px; top: 92px; width: 206px; height: 192px;
    border: 2px solid var(--orange);
    background: linear-gradient(180deg, var(--photo-top), var(--photo-bottom));
  }
  .base { position: absolute; left: 0; bottom: 0; width: 540px; height: 46px; }
  .website {
    position: absolute; right: 30px; bottom: 8px;
    font-size: 12px; letter-spacing: 1px; color: var(--white);
  }

  /* Back side */
  .card-back {
    background: linear-gradient(135deg, #151515, var(--ink) 60%);
    display: flex; align-items: center; justify-content: center;
  }
  .card-back .brand { position: static; gap: 16px; }
  .card-back .brand-mark { width: 42px; height: 42px; }
  .card-back .brand-name { font-size: 28px; color: var(--white); letter-spacing: 3px; }
</style>
</head>
<body>

  <section class="card card-front" aria-label="Visitenkarte Vorderseite">
    <div class="front-shade"></div>

    <div class="brand">
      <span class="brand-mark"></span>
      <span class="brand-name">Lindqvar<br>&amp; Staff</span>
    </div>

    <div class="person">
      <p class="person-name">Jonas Brandt</p>
      <p class="person-role">Managing Director</p>
    </div>
    <div class="divider"></div>

    <ul class="contact">
      <li>
        <svg viewBox="0 0 24 24" aria-hidden="true"><path fill="#EE7325" d="M6.6 10.8a15 15 0 0 0 6.6 6.6l2.2-2.2c.3-.3.7-.4 1-.2 1.1.4 2.3.6 3.6.6.6 0 1 .4 1 1V20c0 .6-.4 1-1 1A17 17 0 0 1 3 4c0-.6.4-1 1-1h3.5c.6 0 1 .4 1 1 0 1.3.2 2.5.6 3.6.1.3 0 .7-.2 1z"/></svg>
        044-870 215 934
      </li>
      <li>
        <svg viewBox="0 0 24 24" aria-hidden="true"><path fill="#EE7325" d="M2 5h20v14H2zm2 2v.4l8 5.1 8-5.1V7z"/></svg>
        info@lindqvar-staff.de
      </li>
    </ul>

    <svg class="base" viewBox="0 0 540 46" preserveAspectRatio="none" aria-hidden="true">
      <path fill="#EE7325" d="M0 32 H230 V38 H0 Z"/>
      <path fill="#0b0b0b" d="M230 46 C245 46 240 24 262 24 H540 V46 Z"/>
    </svg>

    <div class="photo" role="img" aria-label="Porträtfoto des Mitarbeiters im Sakko vor hellgrauem Hintergrund"></div>

    <p class="website">www.lindqvar-staff.de</p>
  </section>

  <section class="card card-back" aria-label="Visitenkarte Rückseite">
    <div class="brand">
      <span class="brand-mark"></span>
      <span class="brand-name">Lindqvar<br>&amp; Staff</span>
    </div>
  </section>

</body>
</html>
```